Generic Business Card

I need a business card for my new cafe which is only six weeks old. I'm continuously asked for a business so that customers can either keep or pass on to a friend. I'd also like a card that I can give out with each bill which contains the business name, address, contact details and website.
The cafe's internal design has an industrial feel to it with modern subdued colours. I have attached an internal photo along with my main hero shot and logo.
The hero shot features prominently on my website and other print material and I would also like it to appear on my bus card.

Target Market(s)

Men & women between 35 and 45 years of age who know and enjoy good coffee.

Industry/Entity Type

Industrial

Contact Information for Business Card

Shop 7b/318-320 Pellimore Road, East Marlowe 3162
Tel. 9452 3170
www.tovasell.com.au

```html
<!DOCTYPE html>
<html lang="en">
<head>
<meta charset="UTF-8">
<title>Tovasell – Business Card</title>
<link rel="stylesheet" href="https://fonts.googleapis.com/css2?family=Questrial&display=swap">
<style>
  :root {
    --card: #ffffff;
    --ink: #1f1f1f;
    --rule: #2a2a2a;
    --photo-dark: #1c1c1c;
    --photo-mid: #6e6e6e;
    --photo-light: #d9d9d9;
  }
  * { margin: 0; padding: 0; box-sizing: border-box; }
  html, body {
    width: 1200px;
    height: 750px;
    overflow: hidden;
    background: var(--card);
  }
  .card {
    position: relative;
    width: 1200px;
    height: 750px;
    background: var(--card);
    font-family: "Questrial", "Century Gothic", sans-serif;
    color: var(--ink);
    overflow: hidden;
  }
  .hero-photo {
    position: absolute;
    left: 0;
    top: 0;
    width: 620px;
    height: 750px;
    background:
      linear-gradient(90deg, rgba(255,255,255,0) 0%, rgba(255,255,255,0) 40%, rgba(255,255,255,0.7) 72%, var(--card) 100%),
      linear-gradient(160deg, var(--photo-light) 0%, var(--photo-mid) 35%, var(--photo-dark) 70%, #3a3a3a 100%);
  }
  .brand {
    position: absolute;
    right: 110px;
    top: 130px;
    width: 560px;
    text-align: right;
  }
  .brand-name {
    font-size: 88px;
    font-weight: 400;
    line-height: 1;
    letter-spacing: 3px;
    text-transform: uppercase;
    white-space: nowrap;
    color: var(--ink);
  }
  .brand-line {
    display: flex;
    align-items: center;
    gap: 16px;
    margin-top: 18px;
  }
  .brand-rule {
    flex: 1;
    height: 3px;
    background: var(--rule);
  }
  .brand-tagline {
    font-size: 32px;
    white-space: nowrap;
    color: var(--ink);
  }
  .contact {
    position: absolute;
    right: 110px;
    top: 430px;
    text-align: right;
    font-size: 30px;
    font-style: normal;
    line-height: 1.3;
    white-space: nowrap;
    color: var(--ink);
  }
</style>
</head>
<body>
  <main class="card">
    <div class="hero-photo" role="img" aria-label="Black and white photo of a barista pulling an espresso shot into a cup at a coffee machine"></div>

    <header class="brand">
      <h1 class="brand-name">Tovasell</h1>
      <div class="brand-line">
        <span class="brand-rule"></span>
        <span class="brand-tagline">eat &amp; drink</span>
      </div>
    </header>

    <address class="contact">
      <p>Shop 7b/318-320 Pellimore Road,</p>
      <p>East Marlowe 3162</p>
      <p>Tel. 9452 3170</p>
      <p>www.tovasell.com.au</p>
    </address>
  </main>
</body>
</html>
```